Insurance Agency website design for Brellow Cover Insurance, LP

Build a website for Brellow Cover Insurance, LP which sells Homeowners, Auto, Renters, Condo, Flood, Disability, Life, Umbrella, and health insurance. We need the coolest insurance agency website out there to get quotes, contact us, or get additional information. Please list the following insurance companies we work with: Varnix, Ostle, Meridale Mutual, Quillor, Dunmarrow, KGZ, and Pellwick.

Make a design similar to https://www.fernagentry.com/

Selling personal insurance policies

```html
<!DOCTYPE html>
<html lang="en">
<head>
<meta charset="utf-8">
<title>Brellow Cover Insurance, LP</title>
<link href="https://fonts.googleapis.com/css2?family=Montserrat:wght@400;500;600;700;800&display=swap" rel="stylesheet">
<style>
:root{
  --blue:#1aa3dc;
  --blue-dark:#0c7fbf;
  --green:#2db36b;
  --navy:#0b1f45;
  --ink:#1d2433;
  --text:#5a6372;
  --light:#f2f4f6;
  --white:#ffffff;
}
*{margin:0;padding:0;box-sizing:border-box}
html,body{width:1200px;height:3428px;overflow:hidden}
body{font-family:"Montserrat",sans-serif;color:var(--ink);background:var(--white);position:relative}
.abs{position:absolute}
.btn{display:inline-block;background:var(--blue);color:var(--white);font-weight:700;font-size:14px;text-transform:uppercase;padding:14px 28px;border-radius:24px;letter-spacing:.3px}

/* header */
.site-header{position:absolute;left:0;top:0;width:1200px;height:132px;background:var(--white)}
.brand{position:absolute;left:120px;top:30px;display:flex;align-items:center;gap:12px}
.brand-dot{width:46px;height:46px;border-radius:50%;background:var(--green)}
.brand-name{font-weight:700;font-size:20px;color:var(--navy);line-height:1.15;width:170px}
.topbar{position:absolute;left:320px;top:0;width:880px;height:34px;background:linear-gradient(90deg,var(--blue-dark),var(--blue));border-bottom-left-radius:30px;display:flex;align-items:center;gap:40px;padding-left:40px;color:var(--white);font-size:14px}
.topbar strong{font-weight:700}
.topbar .item{display:flex;align-items:center;gap:8px}
.ico-circle{width:24px;height:24px;border-radius:50%;background:var(--white);display:flex;align-items:center;justify-content:center}
.main-nav{position:absolute;left:460px;top:72px;display:flex;gap:36px;font-size:14px;font-weight:500;color:var(--ink)}
.main-nav .active{color:var(--blue);border-bottom:2px solid var(--blue);padding-bottom:4px}
.header-quote{position:absolute;right:80px;top:60px}

/* hero */
.hero{position:absolute;left:0;top:132px;width:1200px;height:368px;background:radial-gradient(circle at 72% 45%,#3fc3ff 0%,#1670c8 22%,#0b2f6e 50%,#061633 85%)}
.hero-copy{position:absolute;left:112px;top:80px;width:540px;color:var(--white)}
.hero h1{font-size:40px;font-weight:700;line-height:1.2}
.hero p{font-size:14px;line-height:1.6;margin:20px 0 26px;color:#dce8f7}

/* about */
.about-media{position:absolute;left:120px;top:560px;width:440px;height:640px}
.about-frame{position:absolute;left:0;top:0;width:440px;height:640px;border-radius:0 150px 0 150px;background:var(--blue)}
.about-photo{position:absolute;left:18px;top:0;width:422px;height:622px;border-radius:0 140px 0 140px;background:linear-gradient(160deg,#eef4f7 0%,#b9cfd9 50%,#6e8a97 100%)}
.about-copy{position:absolute;left:624px;top:548px;width:500px}
.section-title{font-size:44px;font-weight:700;color:var(--navy)}
.section-title span{color:var(--blue)}
.about-copy p{font-size:15px;line-height:1.75;color:var(--text);margin:18px 0 26px}

/* coverage band */
.coverage{position:absolute;left:0;top:1320px;width:1200px;height:240px;display:flex}
.coverage-card{width:600px;height:240px;padding:56px 40px 0 40px;color:var(--white);position:relative}
.coverage-card.business{background:var(--green)}
.coverage-card.personal{background:var(--blue);padding-left:60px}
.coverage-card h3{font-size:22px;font-weight:600;margin-bottom:16px}
.coverage-card p{font-size:14px;line-height:1.65;width:450px}
.coverage-badge{position:absolute;left:560px;top:1400px;width:80px;height:80px;border-radius:50%;background:var(--white);display:flex;align-items:center;justify-content:center;box-shadow:0 4px 14px rgba(0,0,0,.15)}

/* carriers */
.carriers-title{position:absolute;left:0;top:1612px;width:1200px;text-align:center}
.carrier-row{position:absolute;left:100px;top:1728px;width:1000px;display:flex;gap:20px}
.carrier{width:184px;height:96px;background:var(--white);border-radius:4px;box-shadow:0 4px 16px rgba(0,0,0,.12);display:flex;align-items:center;justify-content:center;font-size:20px;font-weight:700;color:var(--navy);text-align:center}
.arrow{position:absolute;top:1758px;width:40px;height:40px;border-radius:50%;border:2px solid var(--green);display:flex;align-items:center;justify-content:center}

/* quote */
.quote-copy{position:absolute;left:112px;top:1956px;width:440px}
.quote-copy p{font-size:15px;line-height:1.75;color:var(--text);margin:18px 0 26px}
.quote-media{position:absolute;left:610px;top:1900px;width:460px;height:440px}
.quote-frame{position:absolute;left:0;top:0;width:460px;height:440px;border-radius:0 120px 0 0;background:var(--green)}
.quote-photo{position:absolute;left:0;top:16px;width:444px;height:424px;border-radius:0 110px 0 0;background:linear-gradient(150deg,#d9e7f0 0%,#6b8aa3 45%,#1a2c44 100%)}

/* contact */
.contact{position:absolute;left:0;top:2448px;width:1200px;height:512px;background:linear-gradient(120deg,var(--blue) 0%,#1fb39a 55%,var(--green) 100%)}
.contact h2{position:absolute;left:0;top:70px;width:1200px;text-align:center;font-size:44px;font-weight:600;color:var(--white)}
.field{position:absolute;height:44px;background:var(--white);border-radius:22px;font-size:12px;color:var(--text);padding:14px 22px;text-transform:uppercase}
.field.message{border-radius:18px;height:112px}
.submit{position:absolute;left:524px;top:456px;width:152px;height:44px;border:2px solid var(--white);border-radius:22px;color:var(--white);font-weight:700;font-size:14px;display:flex;align-items:center;justify-content:center}

/* footer */
.site-footer{position:absolute;left:0;top:2960px;width:1200px;height:468px;background:var(--light)}
.footer-brand{position:absolute;left:170px;top:56px;width:240px;display:flex;flex-direction:column;align-items:center;gap:12px;text-align:center}
.footer-brand .brand-dot{width:70px;height:70px}
.socials{position:absolute;left:220px;top:200px;display:flex;gap:22px}
.social{width:28px;height:28px;border-radius:50%;background:var(--blue)}
.footer-col{position:absolute;top:60px}
.footer-col h4{font-size:17px;font-weight:600;color:var(--navy);margin-bottom:18px;letter-spacing:.5px}
.footer-col li{list-style:none;font-size:14px;color:var(--text);margin-bottom:14px;display:flex;align-items:center;gap:10px}
.bullet{width:10px;height:10px;border-radius:50%;background:var(--green)}
.footer-rule{position:absolute;left:120px;top:368px;width:960px;height:1px;background:#d5d9de}
.copyright{position:absolute;left:0;top:394px;width:1200px;text-align:center;font-size:13px;color:var(--text)}
.copyright strong{color:var(--navy)}
</style>
</head>
<body>

<header class="site-header">
  <div class="brand"><div class="brand-dot"></div><div class="brand-name">Brellow Cover Insurance, LP</div></div>
  <div class="topbar">
    <strong>For inquiries, please contact us</strong>
    <div class="item"><span class="ico-circle"><svg width="12" height="12" viewBox="0 0 24 24"><path fill="#1aa3dc" d="M6.6 10.8a15 15 0 006.6 6.6l2.2-2.2c.3-.3.7-.4 1-.2 1.1.4 2.3.6 3.6.6.6 0 1 .4 1 1V20c0 .6-.4 1-1 1A17 17 0 013 4c0-.6.4-1 1-1h3.5c.6 0 1 .4 1 1 0 1.3.2 2.5.6 3.6.1.3 0 .7-.2 1z"/></svg></span>(800) 555-0142</div>
    <div class="item"><span class="ico-circle"><svg width="12" height="12" viewBox="0 0 24 24"><path fill="#1aa3dc" d="M3 5h18v14H3z M3 5l9 7 9-7" stroke="#fff" stroke-width="1.5"/></svg></span>info@brellowcover.com</div>
  </div>
  <nav class="main-nav"><span class="active">HOME</span><span>ABOUT</span><span>SERVICES</span><span>CONTACT US</span></nav>
  <span class="btn header-quote">Get a Quote</span>
</header>

<section class="hero" role="img" aria-label="Glowing digital security shield over a deep blue background">
  <div class="hero-copy">
    <h1>Protect What Matters Most with Brellow Cover Insurance</h1>
    <p>At Brellow Cover Insurance, we understand that your peace of mind is invaluable. Our mission is to protect what matters most to you—your home, your vehicle, your health, and your loved ones.</p>
    <span class="btn">Get Started</span>
  </div>
</section>

<section class="about">
  <div class="about-media">
    <div class="about-frame"></div>
    <div class="about-photo" role="img" aria-label="Protective shield with a check mark above a toy car, a small house and coin stacks"></div>
  </div>
  <div class="about-copy">
    <h2 class="section-title">About <span>Us</span></h2>
    <p>Brellow Cover Insurance is a full-service, independent insurance agency with over three decades of experience in delivering comprehensive insurance solutions to individuals.<br>We proudly offer a diverse portfolio of products from more than 20 of the most reputable and financially secure companies in the industry. Our dedicated team of over 50 skilled professionals is committed to customizing these products and services to meet the unique needs of each client.</p>
    <span class="btn">Read More</span>
  </div>
</section>

<section class="coverage">
  <div class="coverage-card business">
    <h3>Business Insurance</h3>
    <p>Lorem Ipsum is simply dummy text of the printing and typesetting industry. Lorem Ipsum has been the industry's standard dummy text ever since the 1500s.</p>
  </div>
  <div class="coverage-card personal">
    <h3>Personal Insurance</h3>
    <p>Lorem Ipsum is simply dummy text of the printing and typesetting industry. Lorem Ipsum has been the industry's standard dummy text ever since the 1500s.</p>
  </div>
</section>
<div class="coverage-badge"><svg width="40" height="40" viewBox="0 0 24 24"><path d="M12 2l8 3v6c0 5-3.5 9-8 11-4.5-2-8-6-8-11V5z" fill="none" stroke="#2db36b" stroke-width="1.8"/><path d="M8 12l3 3 5-6" fill="none" stroke="#1aa3dc" stroke-width="2"/></svg></div>

<section class="carriers">
  <h2 class="section-title carriers-title">Companies <span>We Work With</span></h2>
  <div class="arrow" style="left:40px"><svg width="14" height="14" viewBox="0 0 24 24"><path d="M15 4l-8 8 8 8" fill="none" stroke="#2db36b" stroke-width="3"/></svg></div>
  <div class="carrier-row">
    <div class="carrier">Varnix</div>
    <div class="carrier">Ostle</div>
    <div class="carrier">Meridale Mutual</div>
    <div class="carrier">Quillor</div>
    <div class="carrier">KGZ</div>
  </div>
  <div class="arrow" style="left:1120px"><svg width="14" height="14" viewBox="0 0 24 24"><path d="M9 4l8 8-8 8" fill="none" stroke="#2db36b" stroke-width="3"/></svg></div>
</section>

<section class="quote">
  <div class="quote-copy">
    <h2 class="section-title">Get a <span>Quote</span></h2>
    <p>We believe that securing your home is one of the most important decisions you can make. Obtaining a comprehensive insurance quote is essential to understanding your coverage options and ensuring that your property is adequately protected against unforeseen events.</p>
    <span class="btn">Get a Quote</span>
  </div>
  <div class="quote-media">
    <div class="quote-frame"></div>
    <div class="quote-photo" role="img" aria-label="Digital security shield glowing above a laptop keyboard"></div>
  </div>
</section>

<section class="contact">
  <h2>Contact Us</h2>
  <div class="field" style="left:220px;top:176px;width:372px">Name</div>
  <div class="field" style="left:612px;top:176px;width:372px">Email</div>
  <div class="field" style="left:220px;top:248px;width:372px">Phone</div>
  <div class="field" style="left:612px;top:248px;width:372px">Subject</div>
  <div class="field message" style="left:220px;top:316px;width:764px">Message</div>
  <div class="submit">SUBMIT</div>
</section>

<footer class="site-footer">
  <div class="footer-brand"><div class="brand-dot"></div><div class="brand-name">Brellow Cover Insurance, LP</div></div>
  <div class="socials"><span class="social"></span><span class="social"></span><span class="social"></span></div>
  <div class="footer-col" style="left:400px">
    <h4>QUICK LINKS</h4>
    <ul><li><span class="bullet"></span>Home</li><li><span class="bullet"></span>About</li><li><span class="bullet"></span>Services</li><li><span class="bullet"></span>Contact Us</li><li><span class="bullet"></span>Get In Touch</li></ul>
  </div>
  <div class="footer-col" style="left:620px">
    <h4>HELP LINKS</h4>
    <ul><li><span class="bullet"></span>Terms of Service</li><li><span class="bullet"></span>Privacy Policy</li><li><span class="bullet"></span>Careers</li><li><span class="bullet"></span>Conditions</li></ul>
  </div>
  <div class="footer-col" style="left:848px">
    <h4>CONTACT US</h4>
    <ul><li><span class="ico-circle" style="background:#dff1f9"><svg width="12" height="12" viewBox="0 0 24 24"><path fill="#1aa3dc" d="M6.6 10.8a15 15 0 006.6 6.6l2.2-2.2c.3-.3.7-.4 1-.2 1.1.4 2.3.6 3.6.6.6 0 1 .4 1 1V20c0 .6-.4 1-1 1A17 17 0 013 4c0-.6.4-1 1-1h3.5c.6 0 1 .4 1 1 0 1.3.2 2.5.6 3.6.1.3 0 .7-.2 1z"/></svg></span>(800) 555-0142</li>
    <li><span class="ico-circle" style="background:#dff1f9"><svg width="12" height="12" viewBox="0 0 24 24"><path d="M3 5h18v14H3z M3 5l9 7 9-7" fill="none" stroke="#1aa3dc" stroke-width="2"/></svg></span>info@brellowcover.com</li></ul>
  </div>
  <div class="footer-rule"></div>
  <p class="copyright">© 2025 <strong>Brellow Cover Insurance, LP</strong> | All Rights Reserved</p>
</footer>

</body>
</html>
```